Corporate Design für logopädische Praxis
Zielgruppe
Ich gründe eine logopädische Praxis, die Sprachtherapie sowohl für Erwachsene als auch Kinder anbietet und damit ein Logo benötigt, das jede Altersgruppe anspricht und 'Lindenhof' als fachliche und menschliche Qualitätszeit interpretiert.
Aufgabenstellung
Ich bevorzuge ein klares Design, welches das Wortspiel der 'Lindenhof' im Idealfall aufgreift und den Patienten vermittelt, dass sowohl die fachliche Qualität der Behandlung als auch die Ebene von Empathie und Patientenorientierung im zwischenmenschlichen Umgang für die Praxis zentral sind.

```html
<!DOCTYPE html>
<html lang="de">
<head>
<meta charset="utf-8">
<title>Lindenhof – Praxis für Logopädie</title>
<link href="https://fonts.googleapis.com/css2?family=Poppins:wght@300;400&display=swap" rel="stylesheet">
<style>
  :root {
    --ink-grey: #8a8b8d;
    --soft-grey: #c4c5c7;
    --lilac: #cfbcd9;
    --periwinkle: #b9bbdc;
    --card-blue: #adaed4;
    --brand: #9d9ccb;
    --text-grey: #8f9093;
    --paper: #ffffff;
    --footer-tint: #f8f8f8;
    --card-light: #ecebf3;
    --stage: #ffffff;
  }
  * { box-sizing: border-box; margin: 0; padding: 0; }
  html, body { width: 1107px; height: 1200px; overflow: hidden; background: var(--stage); }
  body { position: relative; font-family: 'Poppins', sans-serif; font-weight: 300; color: var(--text-grey); }

  /* colour palette */
  .palette { position: absolute; left: 786px; top: 437px; display: flex; height: 70px; }
  .palette span { width: 70.5px; height: 100%; }
  .palette .grey { background: var(--ink-grey); }
  .palette .silver { background: var(--soft-grey); }
  .palette .lilac { background: var(--lilac); }
  .palette .periwinkle { background: var(--periwinkle); }

  /* letterhead */
  .letterhead { position: absolute; left: 62px; top: 464px; width: 497px; height: 704px; background: var(--paper);
    box-shadow: 2px 3px 6px rgba(0,0,0,.28); overflow: hidden; }
  .band-top { position: absolute; left: 0; top: 0; width: 100%; height: 5px;
    background: linear-gradient(to right, var(--lilac) 0 426px, var(--periwinkle) 426px); }
  .brand { position: absolute; left: 0; right: 0; text-align: center; color: var(--brand); }
  .brand .wordmark { display: inline-flex; align-items: center; gap: 6px; font-weight: 300; letter-spacing: .5px; }
  .brand .dot { border-radius: 50%; background: var(--brand); display: inline-block; }
  .brand .tagline { display: block; font-weight: 300; letter-spacing: .4px; }
  .letterhead .brand { top: 22px; }
  .letterhead .wordmark { font-size: 24px; line-height: 30px; }
  .letterhead .dot { width: 9px; height: 9px; }
  .letterhead .tagline { font-size: 8.5px; margin-top: 4px; }

  .tiny { font-size: 5px; line-height: 6px; letter-spacing: .5px; }
  .sender-line { position: absolute; left: 55px; top: 103px; }
  .contact-block { position: absolute; left: 372px; top: 103px; }
  .contact-block .rows { margin-top: 6px; display: grid; grid-template-columns: 46px auto; }
  .contact-block .mail { margin-top: 6px; }

  .fold-mark { position: absolute; left: 0; width: 19px; height: 1px; background: var(--soft-grey); }

  .footer { position: absolute; left: 0; bottom: 0; width: 100%; height: 106px; background: var(--footer-tint); }
  .footer-col { position: absolute; top: 51px; padding-left: 6px; border-left: 1px solid var(--soft-grey); font-size: 4.8px; line-height: 6px; letter-spacing: .4px; }
  .footer-col.legal-left { left: 65px; }
  .footer-col.legal-right { left: 227px; }
  .band-bottom { position: absolute; left: 0; bottom: 0; width: 100%; height: 8px;
    background: linear-gradient(to right, transparent 0 182px, var(--card-blue) 182px 228px, var(--lilac) 228px); }

  /* business cards */
  .card { position: absolute; left: 617px; width: 202px; height: 130px; box-shadow: 2px 3px 6px rgba(0,0,0,.25); overflow: hidden; }
  .card-front { top: 873px; background: var(--card-blue); }
  .card-front .brand { top: 28px; color: var(--paper); }
  .card-front .dot { background: var(--paper); width: 10px; height: 10px; }
  .card-front .wordmark { font-size: 26px; line-height: 32px; }
  .card-front .tagline { font-size: 9px; margin-top: 6px; }
  .card-back { top: 1032px; background: var(--card-light); }
  .card-back .band-bottom { height: 8px;
    background: linear-gradient(to right, transparent 0 61px, var(--card-blue) 61px 82px, var(--lilac) 82px); }
</style>
</head>
<body>

  <div class="palette" aria-label="Farbpalette">
    <span class="grey"></span><span class="silver"></span><span class="lilac"></span><span class="periwinkle"></span>
  </div>

  <section class="letterhead">
    <div class="band-top"></div>

    <div class="brand">
      <span class="wordmark"><span class="dot"></span>Lindenhof</span>
      <span class="tagline">PRAXIS FÜR LOGOPÄDIE</span>
    </div>

    <p class="sender-line tiny">LINDENHOF<br>Ihre Straße 30 &nbsp;|&nbsp; 60325 Ihre Stadt</p>

    <div class="contact-block tiny">
      <p>LINDENHOF<br>Ihre Straße 30<br>60325 Ihre Stadt</p>
      <div class="rows">
        <span>Telefon</span><span>069 41275830</span>
        <span>Telefax</span><span>069 412758390</span>
        <span>Mobil</span><span>015729384615</span>
      </div>
      <p class="mail">info@lindenhof-praxis.de</p>
    </div>

    <span class="fold-mark" style="top:237px"></span>
    <span class="fold-mark" style="top:352px"></span>
    <span class="fold-mark" style="top:474px"></span>

    <div class="footer">
      <p class="footer-col legal-left">LINDENHOF<br>vertreten durch Ihr Name<br>Ihre Straße 30<br>60325 Ihre Stadt</p>
      <p class="footer-col legal-right">Steuernummer 047 381 52640<br>Handelsregister HRB 203415<br>Registergericht Ihre Stadt<br>Ust. IdNr. DE287406153</p>
      <div class="band-bottom"></div>
    </div>
  </section>

  <section class="card card-front">
    <div class="brand">
      <span class="wordmark"><span class="dot"></span>Lindenhof</span>
      <span class="tagline">PRAXIS FÜR LOGOPÄDIE</span>
    </div>
  </section>

  <section class="card card-back">
    <div class="band-bottom"></div>
  </section>

</body>
</html>
```